Velmori Sciences needs high end Label Design for a revolutionary new supplement

We at Velmori Sciences are looking for a brand new Label Design for a first of its kind product called Solvenna. It is the first supplement on the market that treats grief and heartbreak. This product is unisex for both men and woman. We want the New Label to look high end and luxurious using the brand colors which are gold and burgundy. Please feel free to use other colors such as black, white, or gray to go along with it or any other colors if you feel would be a great fit! Velmori Sciences is like the Tarnwick of the supplement world, coming out with new products that will challenge the way people treat different symptoms. To Recap:

1. Product Name: SOLVENNA - the font will play a big roll
2. The Label will be placed on an all white bottle
3. Some parts of the label will be printed with foil to make parts of the label shiny and more attractive. Please keep this in mind when designing.
4. Must use our Logo. I will attach a file of our logo and of the emblem as well. Feel free to use the emblem separately if you have a great idea for it. Please let us know if you need the Logo in a different file type.
5. This all natural herbal supplement in pill form is the first to treat grief and support someone with a broken heart. The consumers purchasing this product will be going through a hard and emotional time. This is a serious product.
6. The manufacturer has included some basic instructions regarding the dye line and file types. Please do your best to meet these. If you cannot meet the guidelines please submit art work anyways. If your design is chosen we will just have the manufacturer replicate the design.

The final label should portray Solvenna and Velmori Sciences as a luxurious brand and product which was made with cutting edge science leading the way with revolutionary ideas. We want customers to feel that the product is worth every penny, because it is. As soon as they receive the product and take one look at the label, I want them to think WOW I made the right choice buying this. I have attached some Label designs that we really liked for your review.

Please feel free to message me with any questions or if you need the Logo in a different file type. Thank you all.
Updates

Please send in more entries while we take a couple days to review, we are still looking for that one design we can work with. We are getting close, thank you all!

Target Market(s)

People going through grief and heartbreak.

Font styles to use
Sans Serif
Script
Other font styles liked:
• Any font that looks good, The font for the name SOLVENNA is very important and will brand it. We hated the font used in the label we received in our first label draft (attached so you can see)

Requirements
Must have
• Must have the company Logo that says the company name
• Must have the colors Gold and Burgundy
• Must have some areas that will be the shiny foil when label is printed.
• Must say "Dietary Supplement" somewhere near the bottom along with "90 Capsules"
• I have attached a Label someone designed for us but were not really happy with. I did like the font the "Dietary supplement" and "90 Capsules" had and also where it was placed. We absolutely HATED the font used for Solvenna.
• Must look at the label design we received from the manufacturer and take into consideration the room needed to write in the directions and all the symbols such as "made in america" and "KMT Facility" Don't worry about adding these in as they will put those in before printing but keep in mind they will be added to the Final Label along with the Supplement Facts.
Nice to have
• Would like to see other colors to go with gold and burgundy suck as black, white, or gray. I have attached some Label designs that I really liked for your reference.
Should not have
• Does not need to have any other legal language, that will be applied by the the manufacturer's graphics team.

```html
<!DOCTYPE html>
<html lang="en">
<head>
<meta charset="utf-8">
<title>Solvenna Label – Velmori Sciences</title>
<link rel="stylesheet" href="https://fonts.googleapis.com/css2?family=Archivo:wght@700&family=Tinos&display=swap">
<style>
  :root {
    --page-bg: #eeeff1;
    --label-navy: #0b1140;
    --label-deep: #03040f;
    --glow-blue: #2a6cf0;
    --glow-cyan: #a9dcff;
    --burgundy-top: #4a0f1c;
    --burgundy-bottom: #12040a;
    --brand-red: #c8141c;
    --brand-red-dark: #5e060c;
    --gold-light: #f6e3a1;
    --gold: #c9a04a;
    --gold-dark: #8a6424;
    --text-white: #ffffff;
  }
  * { box-sizing: border-box; margin: 0; padding: 0; }
  html, body {
    width: 1200px;
    height: 1200px;
    overflow: hidden;
    background: var(--page-bg);
  }
  .label {
    position: absolute;
    left: 0;
    top: 282px;
    width: 1200px;
    height: 636px;
    background: linear-gradient(180deg, var(--label-navy), var(--label-deep));
    overflow: hidden;
  }
  .label__light-rays {
    position: absolute;
    inset: 0;
    background:
      radial-gradient(ellipse 300px 330px at 600px 318px, rgba(169,220,255,0.8), rgba(42,108,240,0.5) 45%, rgba(42,108,240,0) 75%),
      radial-gradient(ellipse 560px 240px at 600px 340px, rgba(42,108,240,0.4), rgba(42,108,240,0) 70%),
      linear-gradient(90deg, rgba(3,4,15,0.6) 0%, rgba(3,4,15,0) 30%, rgba(3,4,15,0) 70%, rgba(3,4,15,0.6) 100%);
  }
  .label__foil-band {
    position: absolute;
    left: 0;
    width: 1200px;
    height: 4px;
    background: linear-gradient(90deg, var(--gold-dark), var(--gold-light) 30%, var(--gold) 55%, var(--gold-light) 75%, var(--gold-dark));
  }
  .label__foil-band--top { top: 0; }
  .label__foil-band--bottom { bottom: 0; }
  .label__diamond {
    position: absolute;
    left: 0;
    top: 0;
    width: 1200px;
    height: 636px;
  }
  .brand {
    position: absolute;
    left: 0;
    width: 1200px;
    top: 158px;
    text-align: center;
  }
  .brand__mark {
    display: block;
    width: 42px;
    height: 42px;
    margin: 0 auto 12px;
    border-radius: 50%;
    background: var(--brand-red);
  }
  .brand__name {
    font-family: "Tinos", serif;
    font-size: 24px;
    line-height: 1;
    letter-spacing: 3px;
    color: var(--gold);
    text-transform: uppercase;
  }
  .product-name {
    position: absolute;
    left: 0;
    width: 1200px;
    top: 290px;
    text-align: center;
    font-family: "Archivo", sans-serif;
    font-weight: 700;
    font-size: 80px;
    line-height: 1;
    color: var(--brand-red);
    text-shadow: 0 2px 0 var(--brand-red-dark);
  }
  .supplement-type {
    position: absolute;
    left: 0;
    width: 1200px;
    top: 402px;
    text-align: center;
    font-family: "Tinos", serif;
    font-size: 20px;
    line-height: 30px;
    color: var(--text-white);
  }
  .capsule-count {
    position: absolute;
    left: 696px;
    top: 546px;
    font-family: "Tinos", serif;
    text-align: left;
  }
  .capsule-count__number {
    display: block;
    font-size: 48px;
    line-height: 1;
    color: var(--gold-light);
  }
  .capsule-count__unit {
    display: block;
    font-size: 15px;
    line-height: 1.2;
    color: var(--text-white);
  }
</style>
</head>
<body>
  <main class="label">
    <div class="label__light-rays" role="img" aria-label="Abstract blue light rays glowing behind the central diamond"></div>
    <div class="label__foil-band label__foil-band--top"></div>
    <div class="label__foil-band label__foil-band--bottom"></div>

    <svg class="label__diamond" viewBox="0 0 1200 636" aria-hidden="true">
      <defs>
        <linearGradient id="burgundyFill" x1="0" y1="0" x2="0" y2="1">
          <stop offset="0" stop-color="var(--burgundy-top)"/>
          <stop offset="1" stop-color="var(--burgundy-bottom)"/>
        </linearGradient>
        <linearGradient id="goldFoil" x1="0" y1="0" x2="1" y2="1">
          <stop offset="0" stop-color="var(--gold-light)"/>
          <stop offset="0.35" stop-color="var(--gold)"/>
          <stop offset="0.55" stop-color="var(--gold-light)"/>
          <stop offset="0.8" stop-color="var(--gold-dark)"/>
          <stop offset="1" stop-color="var(--gold-light)"/>
        </linearGradient>
      </defs>
      <polygon points="600,90 828,318 600,546 372,318" fill="none" stroke="var(--glow-cyan)" stroke-width="16" opacity="0.45"/>
      <polygon points="600,90 828,318 600,546 372,318" fill="url(#burgundyFill)" stroke="url(#goldFoil)" stroke-width="5"/>
      <polygon points="600,106 812,318 600,530 388,318" fill="none" stroke="url(#goldFoil)" stroke-width="1.2" opacity="0.7"/>
    </svg>

    <div class="brand">
      <span class="brand__mark"></span>
      <p class="brand__name">Velmori<br>Sciences</p>
    </div>

    <h1 class="product-name">Solvenna</h1>

    <p class="supplement-type">Dietary<br>Supplement</p>

    <p class="capsule-count">
      <span class="capsule-count__number">90</span>
      <span class="capsule-count__unit">Capsules</span>
    </p>
  </main>
</body>
</html>
```